Business Card

Just need business logo with phone number on it. 0487 312 654
And the following on the bottom of the card.

"Your local plumbing experts".
and emblems for zelpa card, cheque and cash

```html
<!DOCTYPE html>
<html lang="en">
<head>
<meta charset="utf-8">
<title>Northgate Pipeworks – Business Card</title>
<link rel="stylesheet" href="https://fonts.googleapis.com/css2?family=Open+Sans:wght@400;600&family=Russo+One&display=swap">
<style>
  :root {
    --bg: #3b332e;
    --card: #0d0d0d;
    --card-edge: #1a1a1a;
    --red: #e3232b;
    --blue: #1f8fe0;
    --white: #f2f2f2;
    --silver: #c9c9c9;
  }
  * { margin: 0; padding: 0; box-sizing: border-box; }
  html, body { width: 1200px; height: 900px; overflow: hidden; }
  body {
    background: var(--bg);
    font-family: "Open Sans", Arial, sans-serif;
    position: relative;
  }
  .card {
    position: absolute;
    top: 291px;
    width: 540px;
    height: 318px;
    background: var(--card);
    border: 1px solid var(--card-edge);
    border-radius: 4px;
    box-shadow: 0 14px 30px rgba(0,0,0,0.45);
  }
  .card-front { left: 40px; }
  .card-back { left: 620px; }

  .brand-name {
    font-family: "Russo One", Arial, sans-serif;
    font-weight: 400;
    color: var(--red);
    font-size: 34px;
    letter-spacing: 1px;
    line-height: 1.1;
  }
  .card-front .brand {
    position: absolute;
    left: 40px;
    top: 46px;
    display: flex;
    align-items: center;
    gap: 12px;
  }
  .brand-mark {
    width: 18px;
    height: 18px;
    border-radius: 50%;
    background: var(--blue);
  }

  .contact-phone {
    position: absolute;
    left: 40px;
    top: 150px;
    display: flex;
    align-items: center;
    gap: 10px;
    color: var(--white);
    font-size: 22px;
  }
  .phone-icon {
    width: 26px;
    height: 26px;
    border-radius: 50%;
    border: 2px solid var(--red);
    display: flex;
    align-items: center;
    justify-content: center;
  }
  .tagline {
    position: absolute;
    left: 40px;
    bottom: 44px;
    color: var(--white);
    font-size: 21px;
  }

  .payment-methods {
    position: absolute;
    right: 36px;
    top: 148px;
    display: flex;
    gap: 12px;
    align-items: center;
  }
  .payment-name {
    font-family: "Open Sans", Arial, sans-serif;
    font-weight: 600;
    font-size: 18px;
    color: var(--white);
    padding-right: 4px;
  }
  .payment-badge {
    width: 58px;
    height: 34px;
    background: var(--white);
    border-radius: 2px;
    display: flex;
    align-items: center;
    justify-content: center;
  }
  .payment-badge.cheque { background: transparent; }

  .card-back .brand {
    position: absolute;
    inset: 0;
    display: flex;
    align-items: center;
    justify-content: center;
  }
  .card-back .brand-name {
    color: var(--silver);
    font-size: 40px;
  }
</style>
</head>
<body>
  <section class="card card-front" aria-label="Business card front">
    <div class="brand">
      <span class="brand-mark"></span>
      <span class="brand-name">Northgate Pipeworks</span>
    </div>

    <div class="contact-phone">
      <span class="phone-icon">
        <svg width="14" height="14" viewBox="0 0 24 24" aria-hidden="true">
          <path fill="#1f8fe0" d="M6.6 10.8a15.1 15.1 0 0 0 6.6 6.6l2.2-2.2a1 1 0 0 1 1-.25 11.4 11.4 0 0 0 3.6.57 1 1 0 0 1 1 1V20a1 1 0 0 1-1 1A17 17 0 0 1 3 4a1 1 0 0 1 1-1h3.5a1 1 0 0 1 1 1c0 1.25.2 2.45.57 3.57a1 1 0 0 1-.25 1z"/>
        </svg>
      </span>
      <span class="phone-number">0487 312 654</span>
    </div>

    <div class="payment-methods">
      <span class="payment-name">zelpa</span>
      <span class="payment-badge cash" aria-label="Cash">
        <svg width="22" height="22" viewBox="0 0 22 22" aria-hidden="true">
          <circle cx="11" cy="11" r="10" fill="#0d0d0d"/>
          <text x="11" y="15.5" text-anchor="middle" font-family="Arial, sans-serif" font-size="13" font-weight="700" fill="#f2f2f2">$</text>
        </svg>
      </span>
      <span class="payment-badge cheque" aria-label="Cheque">
        <svg width="58" height="34" viewBox="0 0 58 34" aria-hidden="true">
          <g transform="rotate(-10 29 17)" fill="none" stroke="#f2f2f2" stroke-width="2">
            <rect x="5" y="7" width="48" height="22" rx="1"/>
            <line x1="10" y1="14" x2="30" y2="14"/>
            <line x1="10" y1="21" x2="24" y2="21"/>
            <rect x="36" y="18" width="12" height="5"/>
          </g>
        </svg>
      </span>
    </div>

    <p class="tagline">Your local plumbing experts</p>
  </section>

  <section class="card card-back" aria-label="Business card back">
    <div class="brand">
      <span class="brand-name">Northgate Pipeworks</span>
    </div>
  </section>
</body>
</html>
```